Business Card Design

We provide services doing multiple jobs in the construction industry.Please note: The company name needs to be ROCK SOLID BUILDING SERVICESAttached logo was an example of what we wanted. Can you change up the colors?

Industry/Entity Type

Construction

Contact Information for Business Card

ROCK SOLID BUILDING SERVICES5401 HUDSON BEND RDAUSTIN, TX 78734(512)243-6854ROCKSOLIDBUILDINGSERVICES@GMAIL.COM

```html
<!DOCTYPE html>
<html lang="en">
<head>
<meta charset="utf-8">
<title>Pearlwood Framing Works – Business Card</title>
<link rel="stylesheet" href="https://fonts.googleapis.com/css2?family=Jura:wght@500;600;700&display=swap">
<style>
  :root {
    --page: #e4e2df;
    --card-light: #f6f5f2;
    --card-mid: #e9e7e3;
    --ink: #2b2b2d;
    --navy: #23255e;
    --accent-blue: #3a3f9a;
    --band-dark: #2c2b2d;
    --rule: #8a8a8e;
    --white: #ffffff;
  }
  html, body {
    margin: 0;
    padding: 0;
    width: 1200px;
    height: 768px;
    overflow: hidden;
    background: var(--page);
  }
  .card {
    position: absolute;
    left: 100px;
    top: 94px;
    width: 1000px;
    height: 581px;
    border-radius: 22px;
    overflow: hidden;
    background: linear-gradient(135deg, var(--card-light) 0%, var(--card-mid) 100%);
    box-shadow: 0 10px 30px rgba(0,0,0,0.18);
    font-family: "Jura", sans-serif;
    color: var(--ink);
  }
  .brand {
    position: absolute;
    left: 610px;
    top: 70px;
    width: 350px;
    display: flex;
    align-items: center;
    gap: 16px;
    color: var(--navy);
    font-weight: 700;
  }
  .brand-square {
    width: 46px;
    height: 46px;
    flex: none;
    background: var(--navy);
  }
  .brand-name {
    font-size: 40px;
    line-height: 1.05;
    letter-spacing: 1px;
  }
  .brand-name small {
    display: block;
    font-size: 24px;
    letter-spacing: 3px;
  }
  .holder-name {
    position: absolute;
    left: 40px;
    top: 186px;
    margin: 0;
    font-size: 29px;
    font-weight: 600;
    letter-spacing: 2px;
  }
  .holder-title {
    position: absolute;
    left: 40px;
    top: 240px;
    margin: 0;
    font-size: 22px;
    font-weight: 600;
    color: var(--accent-blue);
  }
  .divider {
    position: absolute;
    left: 58px;
    top: 288px;
    width: 870px;
    height: 3px;
    background: linear-gradient(90deg, rgba(138,138,142,0.2), var(--rule) 45%, rgba(138,138,142,0.15));
  }
  .address {
    position: absolute;
    left: 40px;
    top: 380px;
    margin: 0;
    font-size: 23px;
    font-weight: 600;
    line-height: 32px;
    font-style: normal;
  }
  .contacts {
    position: absolute;
    right: 36px;
    top: 312px;
    margin: 0;
    padding: 0;
    list-style: none;
    text-align: right;
    font-weight: 600;
  }
  .contacts li {
    display: flex;
    justify-content: flex-end;
    align-items: center;
    gap: 12px;
  }
  .contacts .phone { font-size: 21px; height: 50px; letter-spacing: 1px; }
  .contacts .web { font-size: 19px; height: 36px; }
  .contacts svg { width: 22px; height: 22px; fill: var(--ink); }
  .footer-dark {
    position: absolute;
    left: 0;
    bottom: 0;
    width: 100%;
    height: 38px;
    background: var(--band-dark);
  }
  .footer-tab {
    position: absolute;
    left: 0;
    bottom: 0;
    width: 430px;
    height: 61px;
  }
  .footer-url {
    position: absolute;
    left: 40px;
    bottom: 14px;
    margin: 0;
    font-size: 20px;
    font-weight: 600;
    letter-spacing: 0.5px;
    color: var(--white);
  }
</style>
</head>
<body>
  <div class="card">
    <div class="brand">
      <span class="brand-square"></span>
      <span class="brand-name">PEARLWOOD<small>FRAMING WORKS</small></span>
    </div>

    <h1 class="holder-name">MARCUS HALLORAN</h1>
    <p class="holder-title">Managing Director</p>
    <div class="divider"></div>

    <address class="address">7732 Fernglen Pass Ln,<br>Suite 18</address>

    <ul class="contacts">
      <li class="phone">(512) 555-0193
        <svg viewBox="0 0 24 24"><path d="M6.6 10.8a15.1 15.1 0 0 0 6.6 6.6l2.2-2.2c.3-.3.7-.4 1-.2 1.1.4 2.3.6 3.6.6.6 0 1 .4 1 1V20c0 .6-.4 1-1 1A17 17 0 0 1 3 4c0-.6.4-1 1-1h3.5c.6 0 1 .4 1 1 0 1.3.2 2.5.6 3.6.1.3 0 .7-.2 1z"/></svg>
      </li>
      <li class="phone">(512) 555-0147
        <svg viewBox="0 0 24 24"><path d="M7 1h10a2 2 0 0 1 2 2v18a2 2 0 0 1-2 2H7a2 2 0 0 1-2-2V3a2 2 0 0 1 2-2zm0 3v14h10V4zm5 15.2a1.2 1.2 0 1 0 0 2.4 1.2 1.2 0 0 0 0-2.4z"/></svg>
      </li>
      <li class="phone">(512) 555-0168
        <svg viewBox="0 0 24 24"><path d="M4 4h5v17H4zM10 8h10v13H10zM12 3h6v4h-6zm0 7v2h2v-2zm4 0v2h2v-2zm-4 4v2h2v-2zm4 0v2h2v-2z"/></svg>
      </li>
      <li class="web">marcus@mailnest.example
        <svg viewBox="0 0 24 24"><path d="M2 5h20v14H2zm2 2v.5l8 5.5 8-5.5V7zm0 2.9V17h16V9.9l-8 5.5z"/></svg>
      </li>
      <li class="web">www.pearlwoodframing.example
        <svg viewBox="0 0 24 24"><path d="M12 2a10 10 0 1 0 0 20 10 10 0 0 0 0-20zm6.9 6h-3a15 15 0 0 0-1.3-4 8 8 0 0 1 4.3 4zM12 4c.8 1.1 1.5 2.5 1.9 4h-3.8c.4-1.5 1.1-2.9 1.9-4zM4.3 14a8 8 0 0 1 0-4h3.4a16 16 0 0 0 0 4zm.8 2h3a15 15 0 0 0 1.3 4 8 8 0 0 1-4.3-4zm3-8h-3a8 8 0 0 1 4.3-4 15 15 0 0 0-1.3 4zM12 20c-.8-1.1-1.5-2.5-1.9-4h3.8c-.4 1.5-1.1 2.9-1.9 4zm2.3-6H9.7a14 14 0 0 1 0-4h4.6a14 14 0 0 1 0 4zm.3 6a15 15 0 0 0 1.3-4h3a8 8 0 0 1-4.3 4zm1.7-6a16 16 0 0 0 0-4h3.4a8 8 0 0 1 0 4z"/></svg>
      </li>
    </ul>

    <div class="footer-dark"></div>
    <svg class="footer-tab" viewBox="0 0 430 61" preserveAspectRatio="none">
      <path d="M0 0H370C392 0 400 10 410 30L430 61H0Z" fill="#c9c8cc"/>
      <path d="M0 0H362C384 0 392 10 402 30L420 61H0Z" fill="var(--navy)"/>
    </svg>
    <p class="footer-url">www.pearlwoodframing.example</p>
  </div>
</body>
</html>
```